Media & Printing Company 6 Page Brochure with a Level Field Theme

We are a printing company that offers most media communication services such as design, web design, mobile app and of course printing. All the profits of the company are used to fund a Level Field Organisation called “Level Field”. We are looking for a 6 page brochure, flat size 630mm x 210mm fold down to 210mm x 210mm. The brochure needs to push the need for companies to use our service on a “Corporate Social Responsibility” basis with losing the site that we are printers and designers.

Looking for a clean design with impact. A file is attached which shows our logo and some copy to give you an idea of what we are.

```html
<!DOCTYPE html>
<html lang="en">
<head>
<meta charset="utf-8">
<title>Brightline Media Communications – Brochure</title>
<link rel="stylesheet" href="https://fonts.googleapis.com/css2?family=Open+Sans:wght@300;400;600&display=swap">
<style>
  :root {
    --page-bg: #f1f1f1;
    --frame: #c9c9c9;
    --sky: #1ba4e6;
    --magenta: #e5007d;
    --yellow: #ffec00;
    --grey-band: #e7e7e7;
    --grey-band-dark: #d9d9d9;
    --ink: #2b2b2b;
    --ink-soft: #555;
    --white: #ffffff;
  }
  * { box-sizing: border-box; margin: 0; padding: 0; }
  html, body { width: 1200px; height: 422px; overflow: hidden; background: var(--page-bg); }
  body { font-family: "Open Sans", Arial, sans-serif; color: var(--ink); position: relative; }

  .brochure {
    position: absolute; left: 20px; top: 22px; width: 1160px; height: 382px;
    background: var(--white); border: 1px solid var(--frame);
  }
  .panel { position: absolute; top: 0; height: 380px; width: 387px; overflow: hidden; }
  .panel--about { left: 0; }
  .panel--services { left: 386px; }
  .panel--sustain { left: 773px; width: 386px; }

  .block { position: absolute; left: 0; width: 100%; }
  .body-copy { position: absolute; font-size: 5.4px; line-height: 1.32; text-align: justify; }
  .art { position: absolute; }

  /* About panel */
  .about-top { top: 0; height: 294px; background: var(--sky); }
  .about-title { position: absolute; left: 17px; top: 128px; font-weight: 300; font-size: 27px; color: var(--white); letter-spacing: -0.3px; }
  .about-copy { left: 210px; top: 18px; width: 166px; color: var(--white); }
  .about-copy .web-link { font-weight: 600; }
  .client-figure { left: 285px; top: 265px; width: 26px; height: 50px; }
  .clients-tab {
    position: absolute; left: 276px; top: 314px; width: 111px; height: 22px;
    background: linear-gradient(180deg, #bdbdbd, #8f8f8f);
    color: var(--ink); font-size: 12.5px; font-weight: 300; line-height: 22px; padding-left: 14px;
  }
  .clients-copy { left: 20px; top: 309px; width: 250px; color: var(--ink); }

  /* Services panel */
  .service-web { top: 0; height: 95px; background: var(--white); }
  .service-design { top: 95px; height: 96px; background: var(--grey-band); }
  .service-print { top: 191px; height: 103px; background: var(--grey-band-dark); }
  .service-digital { top: 294px; height: 86px; background: var(--magenta); }
  .service-label { position: absolute; font-size: 12px; font-weight: 300; color: var(--ink); }
  .service-label--bubble { background: var(--white); border: 1px solid #777; border-radius: 10px; padding: 1px 7px; }
  .service-label--tag { background: var(--white); color: var(--magenta); border-radius: 3px; padding: 1px 7px; font-size: 12.5px; }

  /* Sustainability panel */
  .sustain-top { top: 0; height: 294px; background: var(--yellow); }
  .sustain-title { position: absolute; left: 218px; top: 62px; font-size: 20px; font-weight: 300; color: var(--ink); }
  .sustain-sub { position: absolute; left: 28px; top: 240px; font-size: 15px; font-weight: 300; color: #444; }
  .sustain-copy { left: 185px; top: 137px; width: 193px; color: var(--ink); }
  .digital-heading { position: absolute; left: 30px; top: 301px; font-size: 9.5px; color: var(--ink); }
  .digital-copy { left: 30px; top: 314px; width: 346px; color: var(--ink-soft); }
</style>
</head>
<body>
<main class="brochure">

  <section class="panel panel--about">
    <div class="block about-top">
      <h1 class="about-title">Who are we?</h1>
      <p class="body-copy about-copy">We are an Australian owned and operated unique provider of design, print and web services since 1984. Brightline Media Communications is also a renowned social enterprise supporting Level Field, defending human rights in the hardest places. We give support to the most vulnerable in our community through the work of Level Field. Our Social Responsibility Level Field targets abuse of authority especially for people in mental hospitals and prisons. It empowers the disadvantaged, standing beside them as a community witness and ensuring their involvement in social inclusion programs. iVoice, Level Field is proud to introduce iVoice, the world's first prisoner webpage and interactive email system aimed at empowering people in prisons and forensic hospitals. It brings them into the digital world, reducing the divide and social exclusion that currently exists. FAIR SAY is the only publication that informs people in prisons and hospitals of their rights and reports on current issues facing them. It is distributed to all prisons and hospitals as well as all judges and politicians by name in Australia and New Zealand. <span class="web-link">www.levelfield.org.au</span></p>
      <div class="art client-figure" role="img" aria-label="Silhouette of a business person in a suit" style="background:linear-gradient(180deg,#1b8fd0,#0f6fae);border-radius:12px 12px 3px 3px;"></div>
    </div>
    <div class="clients-tab">Our Clients</div>
    <p class="body-copy clients-copy">We have the privilege of working with some of the most diverse companies in Australia. We don't take this lightly. Whatever the size or nature of your print project, we are here to help. Our clients engage us in all aspects of design, print &amp; web and provide concise and accurate quotations. We view our clients as partners and work closely with them to achieve results they can measure.</p>
  </section>

  <section class="panel panel--services">
    <div class="block service-web">
      <div class="art" role="img" aria-label="Illustration of a figure with colourful butterflies flying from its hands" style="left:18px;top:6px;width:92px;height:80px;background:radial-gradient(circle at 45% 60%,#333 0 14%,transparent 15%),linear-gradient(135deg,#e5007d,#ffec00 40%,#1ba4e6 70%,#7cc242);opacity:.85;border-radius:40% 40% 10% 10%;"></div>
      <span class="service-label service-label--bubble" style="left:70px;top:52px;">Web</span>
      <p class="body-copy" style="left:164px;top:18px;width:214px;">Your website is your virtual office, so believe us when we tell you that IMAGE IS EVERYTHING. It is important whether you're a small business just around the corner or a large organisation with outlets all over Australia.<br>A great website is imagery, functionality and presence. A great website translates to better business.<br><br>We know how to build great websites</p>
    </div>
    <div class="block service-design">
      <p class="body-copy" style="left:31px;top:16px;width:240px;">From cutting edge graphic design to complete company branding or rebranding, we give our customers solutions that surpass their expectations. Brightline Media Communications offers you the talents of our team with the creativity and experience to deliver on your next project. Whether it is website development, illustrations, publications, eBooks, or creating a corporate identity we have the necessary skills.</p>
      <div class="art" role="img" aria-label="Orange butterflies and a pencil drawing a line" style="left:268px;top:22px;width:130px;height:68px;background:linear-gradient(120deg,transparent 10%,#f39a3a 35%,#e5531a 60%,transparent 85%);opacity:.8;border-radius:30%;"></div>
      <span class="service-label service-label--bubble" style="left:258px;top:48px;">Design</span>
    </div>
    <div class="block service-print">
      <div class="art" role="img" aria-label="Swirl of cyan, magenta, yellow and black print ribbons with a butterfly" style="left:14px;top:8px;width:125px;height:95px;background:linear-gradient(150deg,#1ba4e6 20%,#e5007d 45%,#ffec00 65%,#222 85%);border-radius:50% 20% 10% 40%;opacity:.85;"></div>
      <span class="service-label service-label--bubble" style="left:80px;top:52px;">Print</span>
      <p class="body-copy" style="left:162px;top:20px;width:216px;">Brightline Media Communications is a leader in Clean Printing Technologies using environmentally friendly soy inks and best quality papers, with high recycled content where quality isn't compromised. You are in the hands of expert printing industry machinists. We have a complete range of sheetfed offset presses from small to larger A1 size. Our printing equipment and efficient processes mean we can do magazines, brochures and catalogues at competitive rates providing the highest quality standards. As an added touch Brightline can add those special effects such as embossing, foiling, stamping and die-cutting.</p>
    </div>
    <div class="block service-digital">
      <p class="body-copy" style="left:31px;top:12px;width:205px;color:var(--white);">Digital Print is ideal for quick and small print traditional printing methods. We offer fast turn around times and a wide range of stocks from 90gsm to 350gsm paper, card or labels. Even if it's an individualised or personalised piece of work, there are no minimum order and no need to store vast quantities of stock.</p>
      <div class="art" role="img" aria-label="Scattered pastel butterflies in teal, orange and yellow" style="left:238px;top:6px;width:148px;height:80px;background:linear-gradient(135deg,#f7c36b,#8fcfc4 50%,#f4a261);opacity:.75;border-radius:35%;"></div>
      <span class="service-label service-label--tag" style="left:238px;top:50px;">Digital Print</span>
    </div>
  </section>

  <section class="panel panel--sustain">
    <div class="block sustain-top">
      <div class="art" role="img" aria-label="Black butterfly silhouette with a white butterfly in flight" style="left:78px;top:18px;width:130px;height:90px;background:radial-gradient(ellipse at 50% 50%,#111 0 55%,transparent 57%);"></div>
      <h2 class="sustain-title">Sustainability.....</h2>
      <div class="art" role="img" aria-label="Fingerprint made of cyan, magenta, yellow and black lines" style="left:48px;top:118px;width:115px;height:140px;border-radius:48%;background:radial-gradient(circle,#222 0 18%,#e5007d 30%,#1ba4e6 48%,#ffec00 68%);opacity:.8;"></div>
      <div class="sustain-sub">Let's talk printing...</div>
      <p class="body-copy sustain-copy">We purchase our stock from Australian paper suppliers. All stocks are FCC or WCP certified. Recycled stock is readily available ranging from 10% to 100% FCC Certified Stock. The Forest Care Council (FCC) is an independent, non-governmental, not-for-profit organisation that provides standard setting, trademark assurance and certification services for companies interested in responsible forestry. WCP Certified Stock. The Woodland Certification Programme (WCP) is an independent, non-profit, non-governmental organisation, founded in 1999 which promotes sustainably managed forests through independent third party certification. The WCP provides an assurance mechanism to purchasers of paper products that they are promoting the sustainable management of forests. Using FCC and WCP approved stock means that it is from forests that are managed to meet social, ecological and economical needs of present and future generations. With FCC / WCP approved paper you can be confident that you are not contributing to the destruction of the world's forests. Our Product Portfolio Brochures, leaflets, annual reports, calendars, short-run books, letterheads, business cards, corporate stationery, menus... the list goes on. But the bottom line is this. We recognise that the quality of your finished product is the most important consideration. Quality encapsulates your brand values and is integral in promoting your business.</p>
    </div>
    <h3 class="digital-heading">Is digital technology alien to you?</h3>
    <p class="body-copy digital-copy">Brightline Media Communications specialise in professional and effective email marketing campaigns that are custom designed for your business. E-mail marketing is a form of direct marketing which uses electronic mail as a means of communicating commercial or fundraising messages to an audience. It's abbreviation is EDM, email direct marketing. EDM design, creative email marketing and email newsletter template design are just some of the specialist services offered by Brightline Media Communications. Sending a targeted EDM message straight to a potential customer's inbox is a fantastic opportunity to capture their attention, deliver your message and provide them with a clear call to action.</p>
  </section>

</main>
</body>
</html>
```